Promotion material for corporate wellness firm.

I am looking to have a flyer designed that gives some background on the company offerings for corporate wellness. I have attached the content and logo files I would like included and a photo of Maren but if there are other relevant nutrition related photos we would be open to have those included. We are looking for professional but a little light.

Target Market(s)

corporate officers.

Industry/Entity Type

It Company

```html
<!DOCTYPE html>
<html lang="en">
<head>
<meta charset="utf-8">
<title>Maren Halvorsen Wellness – Flyer Options</title>
<link href="https://fonts.googleapis.com/css2?family=Nunito:wght@300;400;600;700;800&display=swap" rel="stylesheet">
<style>
  :root {
    --board-light: #3b3b3d;
    --board-dark: #1b1b1c;
    --green: #2ea443;
    --green-dark: #0f7a34;
    --ink: #3a3a3a;
    --brand-grey: #5f5f62;
    --white: #ffffff;
  }
  html, body {
    margin: 0;
    width: 1200px;
    height: 1200px;
    overflow: hidden;
  }
  body {
    background: radial-gradient(ellipse at 50% 35%, var(--board-light), var(--board-dark) 75%);
    font-family: "Nunito", sans-serif;
    position: relative;
  }
  .option-label {
    position: absolute;
    top: 186px;
    width: 546px;
    text-align: center;
    color: var(--white);
    font-weight: 700;
    font-size: 31px;
    letter-spacing: 1.5px;
  }
  .flyer {
    position: absolute;
    top: 246px;
    width: 546px;
    height: 708px;
    display: block;
    background: var(--white);
  }
  .flyer--one, .label--one { left: 50px; }
  .flyer--two, .label--two { left: 605px; }
  .flyer text { font-family: "Nunito", sans-serif; }
  .name-title { font-weight: 800; fill: var(--white); }
  .credentials { font-weight: 300; fill: var(--white); }
  .contact { font-weight: 600; fill: var(--ink); font-size: 17px; }
  .contact--mail { font-weight: 400; }
  .brand-name { font-weight: 700; fill: var(--brand-grey); font-size: 26px; }
</style>
</head>
<body>
  <div class="option-label label--one">OPTION 1</div>
  <div class="option-label label--two">OPTION 2</div>

  <!-- Flyer option 1 -->
  <svg class="flyer flyer--one" viewBox="0 0 683 884" xmlns="http://www.w3.org/2000/svg">
    <defs>
      <linearGradient id="kitchenTones" x1="0" y1="0" x2="1" y2="1">
        <stop offset="0" stop-color="#e9e2d4"/>
        <stop offset="0.45" stop-color="#8c8379"/>
        <stop offset="0.7" stop-color="#4a57a8"/>
        <stop offset="1" stop-color="#d9c7b0"/>
      </linearGradient>
    </defs>
    <path role="img" aria-label="Photo of Maren smiling in a bright kitchen beside a counter of fresh fruit and vegetables"
          d="M0 0 H683 V312 C560 480 250 580 0 452 Z" fill="url(#kitchenTones)"/>
    <path class="sheen" d="M0 0 H330 C200 30 80 90 0 150 Z" fill="#c9e9c2" opacity="0.6"/>
    <path class="band-main" d="M0 452 C250 580 560 480 683 312 V420 C560 560 300 680 0 722 Z" fill="var(--green)"/>
    <path class="swoosh-upper" d="M420 545 C560 500 640 420 683 312 V360 C620 460 540 520 420 545 Z" fill="var(--green-dark)"/>
    <path class="swoosh-lower" d="M0 735 C180 720 330 680 420 645 C330 700 180 760 0 782 Z" fill="var(--green-dark)"/>
    <path class="leaf" d="M570 560 C600 535 640 540 660 558 C630 578 595 582 570 560 Z" fill="var(--green-dark)"/>
    <path class="leaf" d="M470 455 C505 425 545 430 560 455 C530 480 495 480 470 455 Z" fill="var(--green-dark)"/>
    <rect class="title-bar" x="40" y="568" width="8" height="84" fill="var(--green-dark)"/>
    <text class="name-title" x="62" y="613" font-size="40">Maren Halvorsen</text>
    <text class="credentials" x="62" y="645" font-size="20">M.B.A., R.D., L.D.N.</text>
    <g class="contact-line">
      <circle cx="50" cy="819" r="9" fill="none" stroke="var(--green-dark)" stroke-width="2"/>
      <path d="M46 814 l3 0 l1 3 l-2 1 q1 3 4 4 l1 -2 l3 1 l0 3 q-8 0 -10 -10 z" fill="var(--green-dark)"/>
      <text class="contact" x="66" y="825">3333-333-3333</text>
      <circle cx="220" cy="819" r="9" fill="none" stroke="var(--green-dark)" stroke-width="2"/>
      <rect x="215" y="815" width="10" height="7" fill="none" stroke="var(--green-dark)" stroke-width="1.5"/>
      <text class="contact contact--mail" x="236" y="825">hi@halvorsen.co</text>
    </g>
    <text class="brand-name" x="641" y="795" text-anchor="end">Halvorsen Wellness</text>
  </svg>

  <!-- Flyer option 2 -->
  <svg class="flyer flyer--two" viewBox="0 0 683 884" xmlns="http://www.w3.org/2000/svg">
    <defs>
      <linearGradient id="saladTones" x1="0" y1="0" x2="1" y2="1">
        <stop offset="0" stop-color="#f3ebe4"/>
        <stop offset="0.4" stop-color="#e2b197"/>
        <stop offset="0.75" stop-color="#9fcf6a"/>
        <stop offset="1" stop-color="#e8eef0"/>
      </linearGradient>
    </defs>
    <path role="img" aria-label="Photo of a woman eating a fresh green salad with tomato from a glass bowl"
          d="M0 0 H683 V312 C560 480 250 580 0 452 Z" fill="url(#saladTones)"/>
    <path class="sheen" d="M0 0 H450 C280 20 120 70 0 140 Z" fill="#ffffff" opacity="0.35"/>
    <path class="band-main" d="M0 452 C250 580 560 480 683 312 V420 C560 560 300 680 0 722 Z" fill="var(--green)"/>
    <path class="swoosh-upper" d="M420 545 C560 500 640 420 683 312 V360 C620 460 540 520 420 545 Z" fill="var(--green-dark)"/>
    <path class="swoosh-lower" d="M0 735 C180 720 330 680 420 645 C330 700 180 760 0 782 Z" fill="var(--green-dark)"/>
    <path class="leaf" d="M570 560 C600 535 640 540 660 558 C630 578 595 582 570 560 Z" fill="var(--green-dark)"/>
    <path class="leaf" d="M470 455 C505 425 545 430 560 455 C530 480 495 480 470 455 Z" fill="var(--green-dark)"/>
    <rect class="title-bar" x="40" y="568" width="8" height="84" fill="var(--green-dark)"/>
    <text class="name-title" x="62" y="600" font-size="32" font-weight="600">Maren Halvorsen</text>
    <text class="name-title" x="62" y="646" font-size="48">WELLNESS</text>
    <g class="contact-line">
      <circle cx="50" cy="818" r="9" fill="none" stroke="var(--green-dark)" stroke-width="2"/>
      <path d="M46 813 l3 0 l1 3 l-2 1 q1 3 4 4 l1 -2 l3 1 l0 3 q-8 0 -10 -10 z" fill="var(--green-dark)"/>
      <text class="contact" x="66" y="824">3333-333-3333</text>
      <circle cx="220" cy="818" r="9" fill="none" stroke="var(--green-dark)" stroke-width="2"/>
      <rect x="215" y="814" width="10" height="7" fill="none" stroke="var(--green-dark)" stroke-width="1.5"/>
      <text class="contact contact--mail" x="236" y="824">hi@halvorsen.co</text>
    </g>
    <text class="brand-name" x="641" y="798" text-anchor="end">Halvorsen Wellness</text>
  </svg>
</body>
</html>
```